Reach Crafters Unique Marketing Website Design

I am starting a new company that is a thought leader in the marketing consulting space. The company is called Reach Crafters. We intend to build a Wordpress site on the Astra Theme with the Spectra builder. Our goal is to become the leading voice that empowers high-ticket service business leaders to become Reach Crafters by equipping them with the cutting-edge frameworks and decision grade intelligence taught in leading business schools. What we are looking for is a website design that is clean and professional, making some use of white space well also being eye catching and distinctive in the consulting space. We will probably want to have a video on the homepage not in the hero section, but just below to explain the company and what we do. Our tagline is "Be found. Be chosen." I have attached a brand guide with some messaging, our typography choices, and our color system. The full site will have a primary nav that is four pages - About us, Services, Insights (essentially a blog), and Contact Us. The goal of this project is to develop an art direction that I can give to a designer to build loads of new pages.

Target Market(s)

Business owners (mostly male) from 30-60 years old, looking to fix their sales and marketing funnel.

Industry/Entity Type

Marketing consulting

Font styles to use
Sans Serif

Requirements
Must have
• A clean, professional design that builds trust with owners of high-ticket service businesses. We need a space for explainer video, and sections that tell prospects what we do. Would also like to have a blog carousel.
Nice to have
• Social feeds, if possible. See attached documents for colors and fonts.
Should not have
• Our feel is professional enough to be trustworthy, but unique enough to be memorable. Cartoon ideas do not meet the professional test, and we do not want the website to appear feminine.

```html
<!DOCTYPE html>
<html lang="en">
<head>
<meta charset="utf-8">
<title>Reach Crafters — Be Found. Be Chosen.</title>
<link href="https://fonts.googleapis.com/css2?family=Roboto:wght@400;500;700&family=Roboto+Condensed:wght@300;400&display=swap" rel="stylesheet">
<style>
:root{
  --navy:#0c1530;
  --navy-2:#16244a;
  --blue:#2f55ee;
  --white:#ffffff;
  --ink:#1a1f2e;
  --muted:#3a3f4c;
  --mint:#eef7f3;
  --footer:#2f2f31;
  --line:#e6e9f0;
}
*{margin:0;padding:0;box-sizing:border-box}
html,body{width:1200px;height:3970px;overflow:hidden;background:var(--white)}
body{position:relative;font-family:'Roboto',sans-serif;color:var(--ink)}
.abs{position:absolute}
.hl{color:var(--blue)}
.body-copy{font-family:'Roboto Condensed',sans-serif;font-weight:300;font-size:17px;line-height:37px;color:var(--muted)}
.btn{position:absolute;display:flex;align-items:center;justify-content:center;background:var(--blue);color:var(--white);font-size:13px;font-weight:500;letter-spacing:.3px;border-radius:4px;text-transform:uppercase}
.btn-outline{background:var(--white);color:var(--blue);border:1.5px solid var(--blue)}
.dots{position:absolute;background-image:radial-gradient(#9aa3b8 1.2px,transparent 1.4px);background-size:7px 7px}
.h2{font-size:34px;font-weight:400;letter-spacing:-.5px;text-transform:uppercase;line-height:56px}

/* hero */
.hero{left:0;top:0;width:1200px;height:526px;background:linear-gradient(100deg,#0c1530 0%,#14224a 55%,#27406e 100%);border-bottom-right-radius:28px;overflow:hidden}
.hero-visual{left:632px;top:100px;width:568px;height:426px;background:linear-gradient(160deg,#1c3366 0%,#3e6aa6 50%,#16284f 100%);opacity:.9}
.wordmark{display:flex;align-items:center;gap:10px;font-size:24px;font-weight:500;color:var(--white);letter-spacing:.2px}
.wordmark i{width:14px;height:14px;background:var(--blue);display:block}
.nav{top:40px;left:632px;display:flex;gap:28px;font-size:13px;font-weight:500;color:var(--white)}
.nav .active{color:#7e97ff;background:rgba(47,85,238,.25);padding:0 10px;margin-left:-10px;height:58px;margin-top:-40px;padding-top:40px}
.hero h1{left:108px;top:232px;font-size:40px;font-weight:400;color:var(--white);letter-spacing:-1px}
.hero p{left:110px;top:303px;font-family:'Roboto Condensed',sans-serif;font-weight:300;font-size:15px;line-height:35px;color:var(--white)}

/* problem */
.mint{left:0;top:526px;width:240px;height:698px;background:var(--mint);clip-path:polygon(0 0,100% 50%,0 100%)}
.photo-women{left:111px;top:610px;width:420px;height:530px;border-radius:8px;background:linear-gradient(140deg,#2c6e8a 0%,#1a3c52 45%,#c79b7a 100%)}
.problem-list{left:612px;top:814px;font-family:'Roboto Condensed',sans-serif;font-weight:300;font-size:17px;color:var(--muted);list-style:none}
.problem-list li{height:41px;position:relative;padding-left:60px}
.problem-list li::before{content:"";position:absolute;left:38px;top:8px;width:6px;height:6px;border-radius:50%;background:var(--blue)}

/* why */
.why{left:0;top:1224px;width:1200px;height:598px;background:var(--navy)}
.video{left:120px;top:1574px;width:958px;height:399px;border-radius:14px;background:linear-gradient(120deg,#d9dde4 0%,#a7b0bd 45%,#5c6778 100%)}
.play{left:571px;top:1746px;width:56px;height:56px;border-radius:50%;background:var(--blue);display:flex;align-items:center;justify-content:center}

/* thinks */
.card{position:absolute;top:2164px;width:310px;height:305px;background:var(--white);border-radius:10px;box-shadow:0 2px 14px rgba(20,30,60,.08);text-align:center}
.card h3{margin-top:86px;font-size:17px;font-weight:400;color:var(--blue)}
.card p{margin:14px auto 0;width:270px;font-family:'Roboto Condensed',sans-serif;font-weight:300;font-size:17px;line-height:37px;color:var(--muted)}
.icon-badge{position:absolute;top:2132px;width:80px;height:80px;border-radius:50%;background:var(--navy);display:flex;align-items:center;justify-content:center}
.arrow{position:absolute;width:30px;height:30px;border-radius:50%;border:1.5px solid #333;display:flex;align-items:center;justify-content:center}

/* testimonial */
.testi{left:0;top:2556px;width:1200px;height:430px;background:var(--navy);text-align:center;color:var(--white)}
.dot{position:absolute;top:2906px;width:7px;height:7px;border-radius:50%;border:1px solid var(--blue)}

/* insights */
.insights{left:0;top:2975px;width:1200px;height:690px;background:var(--white);border-top-right-radius:28px}
.post{position:absolute;top:3139px;width:310px;height:426px;background:var(--white);border-radius:10px;box-shadow:0 2px 14px rgba(20,30,60,.08);text-align:center}
.post.featured{background:var(--navy);color:var(--white)}
.post-img{position:absolute;left:10px;top:10px;width:290px;height:193px;border-radius:10px 10px 0 0}
.tag{position:absolute;left:10px;top:10px;height:38px;padding:0 18px;display:flex;align-items:center;background:var(--navy);color:var(--white);font-size:12px;font-weight:500;border-radius:10px 0 16px 0}
.post.featured .tag{background:var(--white);color:var(--navy)}
.post p{position:absolute;left:14px;top:234px;width:282px;font-family:'Roboto Condensed',sans-serif;font-weight:300;font-size:14px;line-height:35.5px;color:var(--muted)}
.post.featured p{color:var(--white)}

/* footer */
.footer{left:0;top:3653px;width:1200px;height:317px;background:var(--footer);border-top-left-radius:28px;color:var(--white)}
.fcol h4{font-size:16px;font-weight:400;color:var(--blue);margin-bottom:22px}
.fcol li{list-style:none;font-family:'Roboto Condensed',sans-serif;font-weight:300;font-size:17px;height:42px}
.social{display:flex;gap:6px}
.social span{width:28px;height:28px;border-radius:50%;border:1.5px solid var(--white);display:flex;align-items:center;justify-content:center}
.social span i{width:8px;height:8px;border-radius:50%;background:var(--white)}
</style>
</head>
<body>

<!-- HERO -->
<section class="abs hero">
  <div class="abs hero-visual" role="img" aria-label="Digital dashboard screen with rising bar chart and growth arrow"></div>
  <div class="abs wordmark" style="left:110px;top:31px"><i></i>Reach Crafters</div>
  <nav class="abs nav">
    <span class="active">HOME</span><span>ABOUT US</span><span>SERVICES</span><span>INSIGHTS</span><span>CONTACT US</span>
  </nav>
  <h1 class="abs">BE FOUND. <span class="hl">BE CHOSEN.</span></h1>
  <p class="abs">We equip founders and partners with the decision-grade marketing intelligence<br>used by elite consulting firms and business schools.</p>
  <div class="btn" style="left:111px;top:400px;width:142px;height:39px">Get in touch</div>
</section>

<!-- PROBLEM -->
<div class="abs mint"></div>
<div class="abs photo-women" role="img" aria-label="Two business women reviewing documents at a laptop"></div>
<h2 class="abs h2" style="left:613px;top:599px;color:var(--ink)">Most firms <span class="hl">don’t have a</span><br><span class="hl">demand</span> problem.</h2>
<p class="abs body-copy" style="left:612px;top:726px;width:500px">High-ticket service firms struggle not because they aren’t good — but because the market doesn’t understand their value.</p>
<ul class="abs problem-list">
  <li>Invisible differentiation</li>
  <li>Inconsistent deal flow</li>
  <li>Founder-dependent sales</li>
  <li>Marketing that doesn’t connect to revenue</li>
</ul>
<p class="abs body-copy" style="left:612px;top:989px;width:500px">Reach Crafters was created to bring the rigor of business school economics and elite consulting strategy into the world of marketing.</p>
<div class="btn" style="left:613px;top:1095px;width:134px;height:39px">Learn more</div>
<div class="dots" style="left:1073px;top:1113px;width:56px;height:32px"></div>

<!-- WHY -->
<section class="abs why">
  <h2 class="abs h2" style="left:112px;top:60px;color:var(--white)">Why <span class="hl">Reach Crafters</span><br>exists</h2>
  <p class="abs body-copy" style="left:556px;top:64px;width:540px;color:var(--white)">Most marketing advice is built for volume businesses. High-ticket firms need something different. In a world flooded with content, ads, and “growth hacks,” even exceptional firms become invisible. Buyers are overwhelmed. Decision-makers default to what feels safe. And differentiation collapses into noise.</p>
  <div class="btn" style="left:556px;top:244px;width:134px;height:38px">Learn more</div>
</section>
<div class="abs video" role="img" aria-label="Explainer video still: team reviewing charts and reports on a desk"></div>
<div class="abs play"><svg width="18" height="18" viewBox="0 0 18 18"><path d="M5 3l10 6-10 6z" fill="#fff"/></svg></div>

<!-- THINKS -->
<div class="dots" style="left:65px;top:2040px;width:56px;height:32px"></div>
<h2 class="abs h2" style="left:0;width:1200px;top:2043px;text-align:center">How <span class="hl">Reach Crafters</span> thinks</h2>

<div class="arrow" style="left:34px;top:2303px"><svg width="12" height="12" viewBox="0 0 12 12"><path d="M8 2L4 6l4 4" stroke="#333" stroke-width="1.5" fill="none"/></svg></div>
<div class="arrow" style="left:1125px;top:2303px"><svg width="12" height="12" viewBox="0 0 12 12"><path d="M4 2l4 4-4 4" stroke="#333" stroke-width="1.5" fill="none"/></svg></div>

<div class="card" style="left:111px"><h3>DECISION-GRADE INTELLIGENCE</h3><p>We use market models, demand data, and buyer behavior analysis to make marketing a business discipline — not a creative gamble.</p></div>
<div class="card" style="left:445px"><h3>CATEGORY-LEVEL POSITIONING</h3><p>We don’t just help you stand out. We help you define the rules of the category so clients naturally see you as the leader.</p></div>
<div class="card" style="left:779px"><h3>DEMAND ARCHITECTURE</h3><p>We design the system that controls how prospects discover, evaluate, and choose you — so growth becomes predictable instead of accidental.</p></div>

<div class="icon-badge" style="left:226px"><svg width="40" height="40" viewBox="0 0 40 40" fill="none" stroke="#fff" stroke-width="1.6"><path d="M13 34v-6c-4-3-5-7-4-11 2-6 8-8 13-7 5 1 8 5 8 10l3 5h-3v4h-5v5"/><path d="M20 12v6l4 3M24 12l-3 3"/></svg></div>
<div class="icon-badge" style="left:560px"><svg width="44" height="44" viewBox="0 0 44 44" fill="none" stroke="#fff" stroke-width="1.6"><circle cx="22" cy="22" r="12"/><circle cx="22" cy="22" r="6"/><circle cx="22" cy="22" r="1.5" fill="#fff"/><path d="M22 4v8M22 32v8M4 22h8M32 22h8"/></svg></div>
<div class="icon-badge" style="left:894px"><svg width="40" height="40" viewBox="0 0 40 40" fill="none" stroke="#fff" stroke-width="1.6"><circle cx="20" cy="10" r="4"/><path d="M14 22c0-4 3-6 6-6s6 2 6 6"/><path d="M6 26l6-2 10 3 8-3 4 2-12 7-10-2-6 1"/></svg></div>

<!-- TESTIMONIAL -->
<section class="abs testi">
  <svg class="abs" style="left:572px;top:128px" width="56" height="42" viewBox="0 0 56 42"><path d="M4 40V24C4 12 10 5 22 2l2 5c-7 2-10 7-10 13h10v20zM32 40V24c0-12 6-19 18-22l2 5c-7 2-10 7-10 13h10v20z" fill="#2f55ee" opacity=".45"/></svg>
  <h2 class="abs h2" style="left:0;width:1200px;top:60px">What <span class="hl">leaders say about</span> Reach Crafters</h2>
  <p class="abs" style="left:0;width:1200px;top:152px;font-size:17px">“THEY DIDN’T GIVE US MARKETING — THEY GAVE US A MARKET.”</p>
  <p class="abs" style="left:190px;width:820px;top:192px;font-family:'Roboto Condensed',sans-serif;font-weight:300;font-size:17px;line-height:37px">Reach Crafters helped us understand how our buyers actually make decisions. Within weeks, we stopped chasing leads and started attracting the exact type of clients we wanted. The clarity alone paid for the engagement.</p>
  <p class="abs hl" style="left:0;width:1200px;top:290px;font-family:'Roboto Condensed',sans-serif;font-weight:300;font-size:17px">Managing Partner, B2B Advisory Firm</p>
</section>
<span class="dot" style="left:563px;background:var(--blue)"></span>
<span class="dot" style="left:586px"></span>
<span class="dot" style="left:609px"></span>
<span class="dot" style="left:632px"></span>

<!-- INSIGHTS -->
<section class="abs insights"></section>
<div class="dots" style="left:1060px;top:3022px;width:56px;height:32px"></div>
<h2 class="abs h2" style="left:0;width:1200px;top:3044px;text-align:center">Latest <span class="hl">insights &amp; blogs</span></h2>

<div class="arrow" style="left:33px;top:3230px"><svg width="12" height="12" viewBox="0 0 12 12"><path d="M8 2L4 6l4 4" stroke="#333" stroke-width="1.5" fill="none"/></svg></div>
<div class="arrow" style="left:1126px;top:3230px"><svg width="12" height="12" viewBox="0 0 12 12"><path d="M4 2l4 4-4 4" stroke="#333" stroke-width="1.5" fill="none"/></svg></div>

<article class="post" style="left:111px">
  <div class="post-img" role="img" aria-label="Presenter leading a strategy meeting in a bright office" style="background:linear-gradient(135deg,#c9d3de,#4c6a8c)"></div>
  <div class="tag">GROWTH STRATEGY</div>
  <p>The typical response is to generate more leads. More traffic. More content. More outbound. But increasing volume only increases noise.</p>
  <div class="btn btn-outline" style="left:89px;top:358px;width:133px;height:38px">Learn more</div>
</article>
<article class="post featured" style="left:445px">
  <div class="post-img" role="img" aria-label="Hands reviewing market reports with charts" style="background:linear-gradient(135deg,#e4e8ee,#7f93b2)"></div>
  <div class="tag">MARKET LEADER</div>
  <p>Behind every dominant consulting firm, advisory group, or professional brand sits an invisible system that controls how buyers discover.</p>
  <div class="btn" style="left:89px;top:358px;width:133px;height:38px">Learn more</div>
</article>
<article class="post" style="left:779px">
  <div class="post-img" role="img" aria-label="Architectural model and sketches on a desk" style="background:linear-gradient(135deg,#eef0f2,#8e99a6)"></div>
  <div class="tag">WELL KNOWN</div>
  <p>The firms that win are not the most visible — they are the most certain. They project a clear point of view about their category, their role</p>
  <div class="btn btn-outline" style="left:89px;top:358px;width:133px;height:38px">Learn more</div>
</article>

<!-- FOOTER -->
<footer class="abs footer">
  <div class="abs wordmark" style="left:112px;top:64px;font-size:28px"><i></i>Reach Crafters</div>
  <div class="abs social" style="left:112px;top:129px"><span><i></i></span><span><i></i></span><span><i></i></span><span><i></i></span><span><i></i></span></div>
  <p class="abs" style="left:112px;top:187px;font-size:14px">© 2026 Reach Crafters. All rights reserved</p>
  <div class="abs fcol" style="left:508px;top:62px"><h4>COMPANY</h4><ul><li>About Us</li><li>Services</li><li>Insights</li><li>Contact</li></ul></div>
  <div class="abs fcol" style="left:725px;top:62px"><h4>EXPERTISE</h4><ul><li>Demand Architecture</li><li>Positioning Strategy</li><li>Revenue Intelligence</li><li>Category Design</li></ul></div>
  <div class="abs fcol" style="left:987px;top:62px"><h4>INSIGHTS</h4><ul><li>Latest Articles</li><li>Demand Models</li><li>Market Strategy</li><li>Leadership</li></ul></div>
</footer>

</body>
</html>
```